Irrigation Business needs their business cards modernised and revamped

I would like to keep my current logo, colours and revamp the format of the card.

I would like the card to be clean yet important.

Im not sure if you include texture but i would like the named logo to be indented into the card etc.

show me something alive and free something thats clinical to the point yet has a feel of achievement. i would like people to go nice card.

Target Market(s)

high end clients, corporate, sports field manger, the guys that make the decisions

Industry/Entity Type

Business

Contact Information for Business Card

nformation to be included

Dean Harlow (Director)
0487305526
dean@kolvat.biz
www.kestonfieldworks.com

instagram logo
google logo
facebook logo

Colors

Designer to choose colors to be used in the design.

Requirements
Nice to have
• indentations a really nice feel to the card good texture

```html
<!DOCTYPE html>
<html lang="en">
<head>
<meta charset="utf-8">
<title>Keston Fieldworks – Business Card</title>
<link rel="stylesheet" href="https://fonts.googleapis.com/css2?family=Open+Sans:wght@400;600;700&family=Montserrat:wght@700&display=swap">
<style>
  :root {
    --backdrop: #1f1f21;
    --green-light: #3fd88e;
    --green-dark: #1f9a55;
    --card-white: #f4f4f2;
    --brand-blue: #2f63ad;
    --drop-blue: #3568b0;
    --drop-rim: #3aa3dc;
    --text-grey: #4a4f57;
    --white: #ffffff;
  }
  * { box-sizing: border-box; margin: 0; padding: 0; }
  html, body { width: 1200px; height: 900px; overflow: hidden; }
  body {
    background: var(--backdrop);
    font-family: "Open Sans", Arial, sans-serif;
    position: relative;
  }
  .card {
    position: absolute;
    left: 270px;
    width: 660px;
    height: 377px;
    border-radius: 4px;
    overflow: hidden;
    box-shadow: 0 10px 24px rgba(0,0,0,.45);
  }
  .card--front {
    top: 50px;
    background: linear-gradient(100deg, var(--green-light) 0%, #2bb36c 45%, var(--green-dark) 100%);
    display: flex;
    flex-direction: column;
    align-items: center;
    justify-content: center;
    color: var(--white);
  }
  .brand-mark {
    width: 86px; height: 86px;
    border: 5px solid var(--white);
    border-radius: 50%;
    margin-bottom: 18px;
  }
  .brand-name {
    font-family: "Montserrat", Arial, sans-serif;
    font-weight: 700;
    font-size: 34px;
    letter-spacing: 1px;
    text-transform: uppercase;
  }
  .social-row { display: flex; gap: 8px; margin-top: 18px; }
  .social-dot { width: 18px; height: 18px; border-radius: 50%; background: var(--white); }

  .card--back {
    top: 473px;
    background: var(--card-white);
  }
  .back-brand {
    position: absolute; left: 46px; top: 88px;
    display: flex; align-items: center; gap: 14px;
  }
  .back-brand .brand-mark {
    width: 66px; height: 66px; margin: 0;
    border: 4px solid var(--brand-blue);
    flex-shrink: 0;
  }
  .back-brand .brand-name {
    color: var(--brand-blue);
    font-size: 26px;
    line-height: 30px;
    width: 200px;
  }
  .contact-list {
    position: absolute; left: 50px; bottom: 40px;
    list-style: none; color: var(--text-grey); font-size: 17px;
  }
  .contact-list li { display: flex; align-items: center; gap: 10px; line-height: 28px; }
  .contact-list svg { width: 15px; height: 15px; fill: var(--brand-blue); }
  .name-badge {
    position: absolute; right: 36px; top: 26px;
    width: 236px; height: 236px; border-radius: 50%;
    background: var(--drop-blue);
    border: 11px solid var(--drop-rim);
    display: flex; flex-direction: column; align-items: center; justify-content: center;
    color: var(--white); text-transform: uppercase; text-align: center;
  }
  .name-badge .person { font-weight: 700; font-size: 17px; }
  .name-badge .role { font-weight: 400; font-size: 16px; }
</style>
</head>
<body>
  <section class="card card--front">
    <div class="brand-mark"></div>
    <div class="brand-name">Keston Fieldworks</div>
    <div class="social-row">
      <span class="social-dot"></span><span class="social-dot"></span><span class="social-dot"></span>
    </div>
  </section>

  <section class="card card--back">
    <div class="back-brand">
      <div class="brand-mark"></div>
      <div class="brand-name">Keston<br>Fieldworks</div>
    </div>

    <ul class="contact-list">
      <li>
        <svg viewBox="0 0 16 16" aria-hidden="true"><path d="M3 1h3l1.5 4-2 1.3a9 9 0 0 0 4.2 4.2L11 8.5l4 1.5v3a2 2 0 0 1-2 2A13 13 0 0 1 1 3a2 2 0 0 1 2-2z"/></svg>
        0487305526
      </li>
      <li>
        <svg viewBox="0 0 16 16" aria-hidden="true"><path d="M1 3h14v10H1z M1 3l7 6 7-6" fill="none" stroke="#2f63ad" stroke-width="1.6"/></svg>
        dean@kolvat.biz
      </li>
      <li>
        <svg viewBox="0 0 16 16" aria-hidden="true"><circle cx="8" cy="8" r="7"/><path d="M1 8h14M8 1c-3 3.5-3 10.5 0 14M8 1c3 3.5 3 10.5 0 14" fill="none" stroke="#f4f4f2" stroke-width="1"/></svg>
        www.kestonfieldworks.com
      </li>
    </ul>

    <div class="name-badge">
      <span class="person">Dean Harlow</span>
      <span class="role">Director</span>
    </div>
  </section>
</body>
</html>
```